BRIGHT CORAL INC , CELL PHONE STORE

We need website design . we already have one but not happy with it www.brightcoralinc.example
we cell phones provide service ,phone repair ,
phone accessories.
online sale payment via PayVerra
shipping by QDMX

Industry/Entity Type

Cell Phone

Number of Pages Required

5+ page

Font styles to use
Serif
Sans Serif

Colors
3176b5

Requirements
Must have
• online sale via PayVerra
Nice to have
• email address

```html
<!DOCTYPE html>
<html lang="en">
<head>
<meta charset="utf-8">
<title>Bright Coral Inc — Cell Phone Store</title>
<link href="https://fonts.googleapis.com/css2?family=Raleway:wght@400;500;600;700&family=Open+Sans:wght@400;600;700&display=swap" rel="stylesheet">
<style>
:root{
  --blue:#3176b5;
  --ink:#333;
  --text:#555;
  --line:#e2e2e2;
  --topbar:#f1f1f1;
  --hero:#eceeef;
  --soft:#f3f3f3;
  --footer:#3a3a3a;
  --footer-base:#2c2c2c;
  --coral:#d9403a;
  --white:#fff;
}
*{box-sizing:border-box;margin:0;padding:0}
html,body{width:1200px;height:2594px;overflow:hidden}
body{position:relative;background:var(--white);font-family:"Open Sans",Arial,sans-serif;color:var(--text)}

/* top bar */
.topbar{position:absolute;left:0;top:0;width:1200px;height:43px;background:var(--topbar);font-size:12px;color:var(--ink)}
.topbar .contact{position:absolute;left:161px;top:13px;display:flex;gap:30px;font-weight:600}
.topbar .contact span b{color:var(--blue);font-weight:400}
.topbar .account{position:absolute;right:161px;top:13px;display:flex;gap:12px;font-size:11.5px}

/* header */
.logo{position:absolute;left:161px;top:68px;font-family:"Raleway",sans-serif;font-weight:700;font-size:24px;color:var(--coral);letter-spacing:.5px}
.search{position:absolute;left:562px;top:63px;width:323px;height:38px;border:1px solid #d6d6d6;background:#fff;font-size:12px;font-style:italic;color:#777;padding:11px 12px}
.search .btn{position:absolute;right:-1px;top:-1px;width:36px;height:38px;background:var(--blue)}
.cart{position:absolute;left:922px;top:62px;display:flex;gap:14px;align-items:center;font-size:11.5px;color:var(--ink);line-height:18px}
.cart .divider{position:absolute;left:-20px;top:0;width:1px;height:40px;background:var(--line)}

/* nav */
.nav{position:absolute;left:0;top:121px;width:1200px;height:52px;background:var(--blue)}
.nav ul{list-style:none;display:flex;position:absolute;left:161px;top:0;height:52px}
.nav li{font-family:"Raleway",sans-serif;font-weight:600;font-size:12.5px;color:#fff;line-height:52px;padding:0 35px}
.nav li.active{background:#5a6f86;padding:0 27px}

/* hero */
.hero{position:absolute;left:0;top:173px;width:1200px;height:456px;background:var(--hero)}
.hero .kicker{position:absolute;left:161px;top:125px;font-family:"Raleway",sans-serif;font-size:21px;color:#444}
.hero h1{position:absolute;left:158px;top:155px;font-family:"Raleway",sans-serif;font-weight:400;font-size:54px;color:#3b5a84;letter-spacing:.5px}
.hero h1 span{color:var(--blue)}
.hero p{position:absolute;left:161px;top:234px;width:450px;font-size:10.5px;line-height:20px;color:#444;letter-spacing:-.1px}
.btn-blue{position:absolute;background:var(--blue);color:#fff;font-family:"Raleway",sans-serif;font-weight:600;font-size:11px;text-align:center}
.hero .btn-blue{left:161px;top:308px;width:96px;height:32px;line-height:32px}
.hero .photo{position:absolute;left:720px;top:62px;width:300px;height:394px;background:linear-gradient(100deg,#d8d8d8 0%,#3a3f47 45%,#1e2126 100%)}
.dots{position:absolute;left:578px;top:385px;display:flex;gap:5px;align-items:center}
.dots i{display:block;width:6px;height:6px;border-radius:50%;background:#ccc}
.dots i.on{width:9px;height:9px;border:2px solid #888;background:transparent}

/* categories */
.cat{position:absolute;top:660px;width:277px;height:225px}
.cat .label{position:absolute;left:24px;top:34px;font-family:"Raleway",sans-serif;font-weight:500;font-size:13px;line-height:22px;color:#444;letter-spacing:.3px;z-index:1}
.cat .visual{position:absolute;right:12px;bottom:0;width:135px;height:165px}

/* featured */
.section-title{font-family:"Raleway",sans-serif;font-weight:700;font-size:21px;color:#444}
.featured-title{position:absolute;left:161px;top:957px}
.arrows{position:absolute;left:976px;top:956px;display:flex;gap:6px}
.arrows span{width:27px;height:27px;border:1px solid #aaa;border-radius:50%;display:flex;align-items:center;justify-content:center}
.product{position:absolute;top:1020px;width:240px;height:245px;text-align:center}
.product .thumb{margin:0 auto;width:120px;height:155px;background:linear-gradient(90deg,#2b2b2b,#5a5a5a 50%,#e8e8e8 52%,#f4f4f4)}
.product .name{margin-top:20px;font-family:"Raleway",sans-serif;font-size:14px;color:#333}
.product .buy{margin-top:20px;display:flex;justify-content:center;align-items:center;gap:16px;font-size:13px;font-weight:600;color:#333}
.product .buy i{display:block;width:34px;height:25px;background:var(--blue)}
.product-sep{position:absolute;top:1022px;width:1px;height:212px;background:var(--line)}

/* services */
.services{position:absolute;left:0;top:1319px;width:1200px;height:388px;background:var(--blue);color:#fff}
.services h2{position:absolute;left:0;width:1200px;top:48px;text-align:center;font-family:"Raleway",sans-serif;font-weight:700;font-size:20px}
.service{position:absolute;top:120px;width:220px;text-align:center}
.service svg{display:block;margin:0 auto}
.service h3{margin-top:14px;font-family:"Raleway",sans-serif;font-weight:600;font-size:14px}
.service p{margin-top:16px;font-size:11px;line-height:20px;color:#e6eef7}
.service .more{margin-top:16px;font-family:"Raleway",sans-serif;font-weight:600;font-size:11px}
.service-sep{position:absolute;top:135px;width:1px;height:190px;background:rgba(255,255,255,.25)}

/* shop */
.shop-photo{position:absolute;left:161px;top:1767px;width:429px;height:260px;background:linear-gradient(135deg,#7a4a2a,#a8723f 40%,#c7b7a6 55%,#6e4326)}
.shop-title{position:absolute;left:622px;top:1774px}
.shop-text{position:absolute;left:622px;top:1810px;width:418px;font-size:10.5px;line-height:20px;color:#444}
.shop .btn-blue{left:622px;top:1980px;width:148px;height:33px;line-height:33px}

/* brands */
.brands{position:absolute;left:0;top:2078px;width:1200px;height:177px;background:var(--soft)}
.brands h2{position:absolute;left:0;width:1200px;top:30px;text-align:center}
.brand{position:absolute;top:83px;width:111px;height:58px;background:#fff;border:1px solid #ddd;display:flex;align-items:center;justify-content:center;font-family:"Raleway",sans-serif;font-weight:700;font-size:16px;color:#222}
.brand-arrow{position:absolute;top:95px}

/* footer */
.footer{position:absolute;left:0;top:2255px;width:1200px;height:280px;background:var(--footer);color:#ccc;font-size:11px}
.footer h4{font-family:"Raleway",sans-serif;font-weight:600;font-size:13.5px;color:#fff;letter-spacing:.3px}
.fcol{position:absolute;top:58px}
.fcol ul{list-style:none;margin-top:20px}
.fcol li{line-height:25px}
.newsletter h4{display:flex;align-items:center;gap:10px;margin-top:-6px}
.newsletter p{margin-top:14px;width:270px;line-height:18px}
.subscribe{display:flex;margin-top:20px}
.subscribe .field{width:177px;height:33px;background:#fff;color:#888;font-size:10.5px;padding:10px 12px}
.subscribe .go{width:75px;height:33px;background:var(--blue);color:#fff;font-family:"Raleway",sans-serif;font-weight:700;font-size:12px;line-height:33px;text-align:center;margin-left:4px}
.social{display:flex;gap:8px;margin-top:12px}
.social i{display:block;width:22px;height:22px;border:1.5px solid #ddd;border-radius:50%}
.contact-col p{margin-top:20px;line-height:18px}
.contact-col p+p{margin-top:10px;line-height:19px}

.base{position:absolute;left:0;top:2535px;width:1200px;height:59px;background:var(--footer-base);color:#ccc;font-size:10.5px}
.base .mark{position:absolute;left:161px;top:19px;font-family:"Raleway",sans-serif;font-weight:700;font-size:16px;color:#fff}
.base .copy{position:absolute;left:330px;top:23px}
.pay{position:absolute;left:830px;top:17px;display:flex;gap:7px;align-items:center}
.pay span{height:24px;padding:0 6px;background:#fff;color:#333;font-family:"Raleway",sans-serif;font-weight:700;font-size:9px;line-height:24px;border-radius:2px}
.base .code{position:absolute;left:1090px;top:23px;color:#fff}
</style>
</head>
<body>

<div class="topbar">
  <div class="contact">
    <span>&#9742; Phone: <b>1 555 010 4841</b></span>
    <span>&#9993; Email: <b>HELLO@BRIGHTCORALINC.EXAMPLE</b></span>
  </div>
  <div class="account"><span>Register</span><span>|</span><span>Login</span><span>Wishlist</span></div>
</div>

<div class="logo">BRIGHT CORAL INC</div>
<div class="search">Search for item
  <div class="btn"><svg width="36" height="38" viewBox="0 0 36 38"><circle cx="17" cy="18" r="5" fill="none" stroke="#fff" stroke-width="2"/><line x1="21" y1="22" x2="25" y2="26" stroke="#fff" stroke-width="2"/></svg></div>
</div>
<div class="cart">
  <span class="divider"></span>
  <svg width="36" height="36" viewBox="0 0 36 36"><path d="M4 12h22l-2 20H6z" fill="var(--blue)"/><path d="M10 12V8a5 5 0 0 1 10 0v4" fill="none" stroke="var(--blue)" stroke-width="2"/><path d="M20 16h14l-2 16H20z" fill="#5b93c7"/></svg>
  <div>Shopping<br>Cart (0) Items</div>
</div>

<nav class="nav"><ul>
  <li class="active">HOME</li><li>ABOUT US</li><li>PHONE REPAIR</li><li>BILL PAYMENT</li><li>AZ</li><li>PRODUCTS</li><li>CONTACT</li>
</ul></nav>

<section class="hero">
  <div class="kicker">Fix Your phone in Your Home!</div>
  <h1>PHONE <span>REPAIR</span></h1>
  <p>Lorem ipsum dolor sit amet, consectetur adipiscing elit, sed do eiusmod tempor incididunt ut labore et dolore magna aliqua. Ut enim ad minim veniam, quis nostrud exercitation ullamco laboris nisi ut aliquip ex ea commodo consequatis aute irure dol.</p>
  <div class="btn-blue">READ MORE</div>
  <div class="photo" role="img" aria-label="Two smartphones with cracked screens"></div>
  <div class="dots"><i></i><i></i><i class="on"></i><i></i></div>
</section>

<div class="cat" style="left:161px;background:#e4e7ea">
  <div class="label">CELL PHONE<br>SERVICE</div>
  <div class="visual" role="img" aria-label="Exploded layers of a phone screen" style="background:linear-gradient(160deg,#cfd4d8,#3b3f44)"></div>
</div>
<div class="cat" style="left:462px;background:#fdf2ea">
  <div class="label">PHONE<br>REPAIR</div>
  <div class="visual" role="img" aria-label="Rose and silver smartphones" style="background:linear-gradient(90deg,#f2c9c0,#e9eef3)"></div>
</div>
<div class="cat" style="left:763px;background:#e4e7ea">
  <div class="label">PHONE<br>ACCESSORIES</div>
  <div class="visual" role="img" aria-label="Red folding tablet cover" style="background:linear-gradient(160deg,#e4e7ea 30%,#d8222a 60%,#b5161d)"></div>
</div>

<h2 class="section-title featured-title">FEATURED PRODUCTS</h2>
<div class="arrows">
  <span><svg width="10" height="10" viewBox="0 0 10 10"><path d="M6 2L3 5l3 3" fill="none" stroke="#666" stroke-width="1.5"/></svg></span>
  <span><svg width="10" height="10" viewBox="0 0 10 10"><path d="M4 2l3 3-3 3" fill="none" stroke="#666" stroke-width="1.5"/></svg></span>
</div>

<div class="product" style="left:110px"><div class="thumb" role="img" aria-label="Black smartphone front and side"></div><div class="name">Screen Replacement</div><div class="buy">£50.00<i></i></div></div>
<div class="product-sep" style="left:358px"></div>
<div class="product" style="left:360px"><div class="thumb" role="img" aria-label="Three smartphones in silver, gold and grey" style="background:linear-gradient(90deg,#dcdcdc,#e9dcc4 50%,#333)"></div><div class="name">Lorem ipsumit amet</div><div class="buy">£50.00<i></i></div></div>
<div class="product-sep" style="left:605px"></div>
<div class="product" style="left:600px"><div class="thumb" role="img" aria-label="Black smartphone front and side"></div><div class="name">Screen Replacement</div><div class="buy">£50.00<i></i></div></div>
<div class="product-sep" style="left:843px"></div>
<div class="product" style="left:840px"><div class="thumb" role="img" aria-label="Glass screen protector over a phone" style="background:linear-gradient(135deg,#f2f4f6,#c9d3dc 50%,#3a3f47)"></div><div class="name">Lorem ipsumit amet</div><div class="buy">£50.00<i></i></div></div>

<section class="services">
  <h2>OUR SERVICES</h2>
  <div class="service" style="left:138px">
    <svg width="56" height="56" viewBox="0 0 56 56" fill="none" stroke="#fff" stroke-width="3"><rect x="6" y="4" width="28" height="44" rx="3"/><rect x="26" y="16" width="22" height="36" rx="3" fill="var(--blue)"/><line x1="33" y1="46" x2="41" y2="46"/></svg>
    <h3>Broken Glass and LCDs</h3>
    <p>Lorem ipsum dolor sit amet, cons ectetur adipiscing elit, sed do eiusm od tempor incididunt ut labore et dolore magna aliquaenim.</p>
    <div class="more">READ MORE</div>
  </div>
  <div class="service-sep" style="left:360px"></div>
  <div class="service" style="left:370px">
    <svg width="56" height="56" viewBox="0 0 56 56" fill="none" stroke="#fff" stroke-width="3"><rect x="18" y="8" width="20" height="40" rx="2"/><line x1="24" y1="4" x2="32" y2="4"/><path d="M30 18l-6 10h8l-6 10" stroke-width="2.5"/><line x1="4" y1="28" x2="12" y2="28"/><line x1="44" y1="28" x2="52" y2="28"/><line x1="8" y1="14" x2="13" y2="18"/><line x1="8" y1="42" x2="13" y2="38"/></svg>
    <h3>Battery Replacement</h3>
    <p>Lorem ipsum dolor sit amet, cons ectetur adipiscing elit, sed do eiusm od tempor incididunt ut labore et dolore magna aliquaenim.</p>
    <div class="more">READ MORE</div>
  </div>
  <div class="service-sep" style="left:596px"></div>
  <div class="service" style="left:607px">
    <svg width="80" height="56" viewBox="0 0 80 56" fill="#fff"><path d="M4 28L28 6l24 22h-6v24H10V28z"/><rect x="40" y="26" width="34" height="24" rx="3" fill="#fff" stroke="var(--blue)" stroke-width="2"/><circle cx="57" cy="38" r="7" fill="var(--blue)"/><circle cx="57" cy="38" r="4" fill="#fff"/></svg>
    <h3>Button Replacement</h3>
    <p>Lorem ipsum dolor sit amet, cons ectetur adipiscing elit, sed do eiusm od tempor incididunt ut labore et dolore magna aliquaenim.</p>
    <div class="more">READ MORE</div>
  </div>
  <div class="service-sep" style="left:836px"></div>
  <div class="service" style="left:842px">
    <svg width="56" height="56" viewBox="0 0 56 56" fill="none" stroke="#fff" stroke-width="3"><path d="M8 6h28l-4 44H12z"/><path d="M10 24h24"/><path d="M44 30c-5 8-7 11-7 15a7 7 0 0 0 14 0c0-4-2-7-7-15z" fill="#fff"/></svg>
    <h3>Water Damage</h3>
    <p>Lorem ipsum dolor sit amet, cons ectetur adipiscing elit, sed do eiusm od tempor incididunt ut labore et dolore magna aliquaenim.</p>
    <div class="more">READ MORE</div>
  </div>
</section>

<div class="shop">
  <div class="shop-photo" role="img" aria-label="Hands repairing a cracked phone screen on a wooden table"></div>
  <h2 class="section-title shop-title">OUR BRIGHT CORAL SHOP</h2>
  <p class="shop-text">Lorem ipsum dolor sit amet, consectetur adipiscing elit, sed do eiusmod tempor ici didunt ut labore et dolore magna aliquat enim ad minim veniam, quis nostrud exlo er citation ullamco laboris nisi ut aliquip ex ea commodo consequatis aute irure dol orem ipsum dolor sit amet, consectetur adipiscing elit, sed do eiusmod tempor inci didunt ut labore et dolore magna aliquat enim ad minim veniam, quis nostrud exloe ritation ullamco laboris nisi ut aliquip ex ea commodo consequatis aute irure dolcita tion ullamco laboris nisi ut aliquip ex ea commodo consequatis.</p>
  <div class="btn-blue">VIEW OUR LOCATION</div>
</div>

<section class="brands">
  <h2 class="section-title">TOP BRANDS</h2>
  <svg class="brand-arrow" style="left:100px" width="24" height="44" viewBox="0 0 24 44"><path d="M20 2L4 22l16 20" fill="none" stroke="#ccc" stroke-width="2"/></svg>
  <div class="brand" style="left:160px">Tablo</div>
  <div class="brand" style="left:287px">Kestrel</div>
  <div class="brand" style="left:415px">Netwave</div>
  <div class="brand" style="left:543px">Telvia</div>
  <div class="brand" style="left:671px">Orbitel</div>
  <div class="brand" style="left:799px">Sorano</div>
  <div class="brand" style="left:927px">Fonex</div>
  <svg class="brand-arrow" style="left:1060px" width="24" height="44" viewBox="0 0 24 44"><path d="M4 2l16 20L4 42" fill="none" stroke="#ccc" stroke-width="2"/></svg>
</section>

<footer class="footer">
  <div class="fcol newsletter" style="left:161px">
    <h4><svg width="24" height="24" viewBox="0 0 24 24"><rect x="1" y="3" width="22" height="18" rx="2" fill="var(--blue)"/><path d="M4 8l8 6 8-6" fill="none" stroke="#fff" stroke-width="2"/></svg>NEWSLETTER</h4>
    <p>Lorem ipsum dolor sit amet, consectetur adipiscing elidolor sit ametdolor sit amet, cons.</p>
    <div class="subscribe"><div class="field">Email Address</div><div class="go">SUBMIT</div></div>
    <div class="social"><i></i><i></i><i></i><i></i><i></i></div>
  </div>
  <div class="fcol contact-col" style="left:474px">
    <h4>CONTACT US</h4>
    <p>Feel free to contact us via phone,email<br>or just send us mail.</p>
    <p>48 Harbor Lane LAKEVIEW, ST 00000.<br>Phone:1 555 010 4841<br>Email: HELLO@BRIGHTCORALINC.EXAMPLE</p>
  </div>
  <div class="fcol" style="left:745px">
    <h4>CUSTOMER SERVICE</h4>
    <ul><li>Contact Us</li><li>Privacy Policy</li><li>Terms &amp; Conditions</li></ul>
  </div>
  <div class="fcol" style="left:942px">
    <h4>QUICK LINKS</h4>
    <ul><li>Login</li><li>New Customers</li><li>Products</li><li>Phone Repair</li></ul>
  </div>
</footer>

<div class="base">
  <div class="mark">BRIGHT CORAL INC</div>
  <div class="copy">©2017 Bright Coral Inc - all rights reserved</div>
  <div class="pay">
    <span>QDMX</span><span>Vantra</span><span>Mercato</span><span>PayVerra</span><span>Skyvo</span>
  </div>
  <div class="code">C4</div>
</div>

</body>
</html>
```